Brintel Works - Fast, Efficient and Gas Mainteance for Domestic, Commercial and Industrial clients

We are in the process of purchasing a new business and would like to get a new logo and business card.
Business is a gas maintenance business that also does new gas installations.
Has been established since 1988.
Services include:
Install all types of gas appliances & equipment inc. hot water units
Maintain / repair / replace all types of gas appliances & equipment

Target Market(s)

Domestic, Commercial and Industrial clients

Industry/Entity Type

Business

Contact Information for Business Card

admin@brintelworks.com.au
07 3918 4726
Brintel Works PTY LTD

Logo Text

Gas Fitting & Plumbing Maintenance Specialists

Font styles to use
Sans Serif

Requirements
Must have
• Logo
• Business name, contact number, email address, web address
• Domestic | Commercial | Industrial Est Since 1988
Nice to have
• Possibly a black card with a flame logo to one side
Should not have
• Spelling errors

```html
<!DOCTYPE html>
<html lang="en">
<head>
<meta charset="utf-8">
<title>Brintel Works – Business Card</title>
<link rel="stylesheet" href="https://fonts.googleapis.com/css2?family=Open+Sans:wght@400;600;700&display=swap">
<style>
  :root {
    --bg: #2f2926;
    --card: #111111;
    --card-edge: #1b1b1b;
    --yellow: #ffd200;
    --red: #e42326;
    --orange: #f47b20;
    --white: #f4f4f4;
    --font: "Open Sans", Arial, sans-serif;
  }
  * { box-sizing: border-box; margin: 0; padding: 0; }
  html, body { width: 1200px; height: 844px; overflow: hidden; }
  body {
    background: var(--bg);
    font-family: var(--font);
    display: flex;
    align-items: center;
    justify-content: center;
    gap: 40px;
  }
  .card {
    position: relative;
    width: 540px;
    height: 310px;
    background: radial-gradient(circle at 50% 35%, #2a2a2a 0%, var(--card) 65%);
    border: 1px solid var(--card-edge);
    overflow: hidden;
  }

  /* Back: contact side */
  .card--back .band {
    position: absolute;
    left: 0; right: 0;
    height: 12px;
    background: var(--yellow);
  }
  .card--back .band--top { top: 0; }
  .card--back .band--bottom { bottom: 0; }
  .contact {
    position: absolute;
    right: 190px;
    top: 78px;
    text-align: right;
    color: var(--white);
    font-size: 15px;
    line-height: 1.45;
  }
  .contact .address { margin-bottom: 26px; }

  /* Front: identity side */
  .tab {
    position: absolute;
    width: 22px;
    height: 36px;
    background: var(--yellow);
  }
  .tab::after {
    content: "";
    position: absolute;
    top: 0; bottom: 0;
    width: 4px;
    background: var(--red);
  }
  .tab--left { left: 0; top: 150px; }
  .tab--left::after { right: -4px; }
  .tab--right { right: 0; top: 24px; }
  .tab--right::after { left: -4px; }

  .identity {
    position: absolute;
    left: 0; right: 0;
    top: 92px;
    display: flex;
    align-items: center;
    justify-content: center;
    gap: 14px;
  }
  .identity .mark {
    width: 26px;
    height: 26px;
    background: var(--red);
  }
  .identity .name {
    color: var(--yellow);
    font-size: 40px;
    font-weight: 400;
    letter-spacing: 0.5px;
  }
  .entity {
    position: absolute;
    left: 0; right: 0;
    top: 150px;
    text-align: center;
    color: var(--yellow);
    font-size: 13px;
    letter-spacing: 4px;
  }
  .sectors {
    position: absolute;
    left: 0; right: 0;
    bottom: 56px;
    text-align: center;
    color: var(--yellow);
    font-size: 14px;
    font-weight: 700;
  }
</style>
</head>
<body>
  <section class="card card--back" aria-label="Card back with contact details">
    <div class="band band--top"></div>
    <div class="contact">
      <p class="address">12345, Address Goes Here<br>Country Name, 123456</p>
      <p class="phone">07 3918 4726</p>
      <p class="email">admin@brintelworks.com.au</p>
      <p class="web">www.brintelworks.com.au</p>
    </div>
    <div class="band band--bottom"></div>
  </section>

  <section class="card card--front" aria-label="Card front with business name">
    <div class="tab tab--right"></div>
    <div class="tab tab--left"></div>
    <div class="identity">
      <span class="mark"></span>
      <span class="name">Brintel Works</span>
    </div>
    <p class="entity">PTY LTD</p>
    <p class="sectors">Domestic | Commercial | Industrial Est Since 1988</p>
  </section>
</body>
</html>
```